New Zealand Marlborough Sauvignon Blanc wine packaging design

We need packaging design for our new wine brand, Dunmore Vale. The wine is a New Zealand Marlborough Sauvignon Blanc. We would like the packaging will portray elegance and style with an understated label. We are looking for a label that portrays the elegance of the French Riviera. The label should be round or pill shaped.
Updates

Industry/Entity Type

Wine

Font styles to use
Serif
Sans Serif

Requirements
Must have
• The words in order of importance: Dunmore Vale, Sauvignon Blanc, Marlborough, New Zealand. It should be fit to the bottle posted in the links
Nice to have
• a pill shape or circular shape
Should not have
• Illustrations of wine bottles, wine glasses, or grapes

```html
<!DOCTYPE html>
<html lang="en">
<head>
<meta charset="utf-8">
<title>Dunmore Vale Sauvignon Blanc Label</title>
<link href="https://fonts.googleapis.com/css2?family=Cinzel:wght@400&family=Oswald:wght@300;400&family=Playfair+Display:wght@400&display=swap" rel="stylesheet">
<style>
  :root {
    --paper: #ffffff;
    --frame: #a4a9ab;
    --ink: #9a9fa1;
    --rule: #b4b8ba;
    --art-green: #a9c59a;
    --art-orange: #efb07a;
    --art-blue: #8fb4d3;
  }
  * { margin: 0; padding: 0; box-sizing: border-box; }
  html, body {
    width: 1200px; height: 675px; overflow: hidden;
    background: var(--paper);
  }
  .canvas {
    position: relative; width: 1200px; height: 675px;
    background: var(--paper);
  }
  .label {
    position: absolute; left: 432px; top: 69px;
    width: 336px; height: 537px;
    border: 3.5px solid var(--frame);
    border-radius: 168px;
    background: var(--paper);
  }
  .label-inner {
    position: absolute; inset: 9px;
    border: 1px solid var(--frame);
    border-radius: 158px;
    overflow: hidden;
  }
  .region {
    position: absolute; top: 64px; left: 0; right: 0;
    text-align: center;
  }
  .region-name {
    font-family: "Playfair Display", serif;
    font-size: 19px; color: var(--ink);
    letter-spacing: -0.02em; line-height: 1;
  }
  .region-rule {
    width: 158px; height: 1px; margin: 4px auto 0;
    background: var(--rule);
  }
  .region-country {
    font-family: "Oswald", sans-serif; font-weight: 400;
    font-size: 9px; letter-spacing: 0.12em; color: var(--ink);
    margin-top: 3px;
  }
  .brand {
    position: absolute; top: 138px; left: 0; right: 0;
    text-align: center; white-space: nowrap;
    font-family: "Cinzel", serif; font-weight: 400;
    color: var(--ink); font-size: 56px; line-height: 56px;
  }
  .brand span { display: block; }
  .varietal {
    position: absolute; top: 285px; left: 16px; right: 16px;
    border-top: 1px solid var(--rule);
    border-bottom: 1px solid var(--rule);
    height: 43px;
    display: flex; align-items: center; justify-content: center;
    white-space: nowrap;
    font-family: "Oswald", sans-serif; font-weight: 300;
    font-size: 15px; letter-spacing: 0.72em; color: var(--ink);
    padding-left: 0.72em;
  }
  .botanical-art {
    position: absolute; left: 0; right: 0; top: 338px; bottom: 0;
    background:
      linear-gradient(180deg, rgba(255,255,255,1) 0%, rgba(255,255,255,0) 45%),
      linear-gradient(90deg, var(--art-green) 0%, var(--art-blue) 35%, var(--art-orange) 65%, var(--art-green) 100%);
    opacity: 0.75;
  }
</style>
</head>
<body>
<div class="canvas">
  <div class="label">
    <div class="label-inner">
      <div class="region">
        <div class="region-name">Marlborough</div>
        <div class="region-rule"></div>
        <div class="region-country">NEW ZEALAND</div>
      </div>
      <h1 class="brand"><span>Dunmore</span><span>Vale</span></h1>
      <div class="varietal">SAUVIGNON BLANC</div>
      <div class="botanical-art" role="img" aria-label="Watercolour botanical border of peacock feathers, orange blossoms, berries and leafy stems"></div>
    </div>
  </div>
</div>
</body>
</html>
```